business card for a massage therapy practice named 'Cedar and Willow Massage Studio'

I really need a trendy, yet easy on the eyes business card to complement my logo. Ideally with some gold or rose gold foil work.

My uploaded file of the logo I have in horizontal but I have a vertical version as well. Another color that is used in the website is a blush pink here and there. I'd like to see some trendy tropical leaves in the design.

```html
<!DOCTYPE html>
<html lang="en">
<head>
<meta charset="utf-8">
<title>Cedar and Willow Massage Studio – Business Card</title>
<link rel="stylesheet" href="https://fonts.googleapis.com/css2?family=Amatic+SC:wght@700&family=Jost:wght@400;500;600&display=swap">
<style>
  :root {
    --backdrop: #a4a4a4;
    --card: #ffffff;
    --leaf-deep: #4a6a45;
    --leaf-soft: #678264;
    --pineapple: #e2ddd2;
    --gold: #8d7547;
    --ink: #555555;
    --logo-ink: #1c1c1c;
    --teal: #6fcdb4;
  }
  * { margin: 0; padding: 0; box-sizing: border-box; }
  html, body { width: 1200px; height: 1200px; overflow: hidden; }
  body { background: var(--backdrop); font-family: "Jost", sans-serif; position: relative; }

  .card {
    position: absolute;
    left: 246px;
    width: 680px;
    height: 390px;
    background: var(--card);
    overflow: hidden;
  }
  .card--front { top: 171px; }
  .card--back { top: 654px; }

  .card__art { position: absolute; inset: 0; width: 100%; height: 100%; }

  .front__name {
    position: absolute; left: 0; width: 668px; top: 122px;
    text-align: center;
    font-family: "Amatic SC", sans-serif; font-weight: 700;
    font-size: 46px; letter-spacing: 1px; color: var(--gold);
  }
  .front__role {
    position: absolute; left: 0; width: 680px; top: 178px;
    text-align: center; font-size: 18px; letter-spacing: 1px; color: var(--gold);
  }
  .front__contact {
    position: absolute; left: 0; width: 668px; top: 245px;
    text-align: center; color: var(--ink); font-size: 18px; line-height: 24px; letter-spacing: 0.8px;
  }
  .front__phone { font-size: 21px; }

  .back__brand {
    position: absolute; left: 0; width: 680px; top: 198px;
    display: flex; justify-content: center; align-items: center; gap: 14px;
  }
  .back__brand-dot { width: 22px; height: 22px; border-radius: 50%; background: var(--gold); }
  .back__brand-name { font-size: 28px; font-weight: 500; color: var(--logo-ink); }
  .back__web {
    position: absolute; left: 0; width: 680px; top: 334px;
    text-align: center; font-size: 16px; font-weight: 600; letter-spacing: 1px; color: var(--teal);
  }
</style>
</head>
<body>

<section class="card card--front">
  <svg class="card__art" viewBox="0 0 680 390">
    <g role="img" aria-label="Faint illustrated pineapples">
      <ellipse cx="115" cy="280" rx="55" ry="75" transform="rotate(30 115 280)" fill="var(--pineapple)"/>
      <ellipse cx="160" cy="170" rx="28" ry="55" transform="rotate(35 160 170)" fill="var(--pineapple)" opacity="0.8"/>
      <ellipse cx="545" cy="140" rx="55" ry="75" transform="rotate(-35 545 140)" fill="var(--pineapple)"/>
      <ellipse cx="490" cy="45" rx="28" ry="50" transform="rotate(-40 490 45)" fill="var(--pineapple)" opacity="0.8"/>
    </g>
    <g role="img" aria-label="Illustrated tropical monstera leaves framing the card">
      <ellipse cx="30" cy="35" rx="82" ry="70" fill="var(--leaf-deep)"/>
      <ellipse cx="20" cy="190" rx="60" ry="100" fill="var(--leaf-deep)"/>
      <ellipse cx="70" cy="395" rx="95" ry="62" fill="var(--leaf-deep)"/>
      <ellipse cx="630" cy="60" rx="100" ry="75" fill="var(--leaf-deep)"/>
      <ellipse cx="635" cy="220" rx="80" ry="95" fill="var(--leaf-deep)"/>
      <ellipse cx="615" cy="400" rx="95" ry="45" fill="var(--leaf-deep)"/>
    </g>
  </svg>
  <h1 class="front__name">Mara Lindqvist</h1>
  <p class="front__role">Make-Up-Artist</p>
  <p class="front__contact">
    <span class="front__phone">310.555.0142</span><br>
    mara@AmberBloomStudio.com<br>
    www.AmberBloomStudio.com
  </p>
</section>

<section class="card card--back">
  <svg class="card__art" viewBox="0 0 680 390">
    <g role="img" aria-label="Row of illustrated monstera leaves along the top edge">
      <ellipse cx="55" cy="40" rx="105" ry="95" fill="var(--leaf-deep)"/>
      <ellipse cx="245" cy="30" rx="100" ry="100" fill="var(--leaf-soft)"/>
      <ellipse cx="455" cy="25" rx="110" ry="85" fill="var(--leaf-soft)"/>
      <ellipse cx="640" cy="20" rx="95" ry="80" fill="var(--leaf-deep)"/>
    </g>
  </svg>
  <div class="back__brand">
    <span class="back__brand-dot"></span>
    <span class="back__brand-name">Cedar and Willow Massage Studio</span>
  </div>
  <p class="back__web">www.yourwebsite.com</p>
</section>

</body>
</html>
```